Heron Haulage needs Bussiness cards!

Our new trucking company needs business cards!
We need the same design with two different names and emails, everything else it's the same.
I have included our original logo so we can use it for the design.
Note: the logo to be used is the o e with the buffalo on the right side, next to the letters H and H.

Target Market(s)

Trucking, refrigerated transportation, freight

Industry/Entity Type

Business

Contact Information for Business Card

Card #1:
Marcus Whitfield
marcuswhitfield@heronhaulage.example
1-855-317-6094
(956)238-7160
4117 W. Larkin Ave.
Pharr, TX 78590
www.heronhaulage.example

Card#2:
Rosalba Quintero
rosalba@heronhaulage.example
1-855-317-6094
(956)238-7160
4117 W. Larkin Ave.
Pharr, TX 78590
www.heronhaulage.example

Font styles to use
Sans Serif

Colors
0655a3
ec1f27
ffffff

Requirements
Must have
• our logo
Nice to have
• roads on background,

```html
<!DOCTYPE html>
<html lang="en">
<head>
<meta charset="utf-8">
<title>Heron Haulage — Business Cards</title>
<link rel="stylesheet" href="https://fonts.googleapis.com/css2?family=Source+Sans+3:wght@400;600;800&display=swap">
<style>
  :root {
    --backdrop: #919191;
    --card-white: #ffffff;
    --navy: #062d5c;
    --brand-red: #b8141e;
    --text-grey: #4a4a4a;
  }
  * { box-sizing: border-box; margin: 0; padding: 0; }
  html, body { width: 1200px; height: 900px; overflow: hidden; }
  body {
    background: var(--backdrop);
    font-family: "Source Sans 3", Arial, sans-serif;
    position: relative;
  }
  .card {
    position: absolute;
    top: 306px;
    width: 440px;
    height: 271px;
    border-radius: 12px;
  }
  .card-front { left: 149px; background: var(--card-white); }
  .card-back { left: 608px; background: var(--navy); }

  .wordmark {
    position: absolute;
    left: 0; right: 0;
    display: flex;
    align-items: center;
    justify-content: center;
    gap: 12px;
    font-weight: 800;
    font-size: 44px;
    line-height: 1;
    letter-spacing: -0.5px;
  }
  .wordmark-mark {
    width: 22px; height: 22px;
    border-radius: 50%;
    flex: none;
  }
  .card-front .wordmark { top: 62px; color: var(--navy); }
  .card-front .wordmark-mark { background: var(--brand-red); }
  .card-back .wordmark { top: 113px; color: var(--card-white); }
  .card-back .wordmark-mark { background: var(--brand-red); }

  .holder-name {
    position: absolute;
    left: 55px; top: 168px;
    color: var(--brand-red);
    font-weight: 600;
    font-size: 15px;
  }
  .address {
    position: absolute;
    left: 55px; top: 200px;
    color: var(--text-grey);
    font-size: 12.5px;
    line-height: 16px;
    font-style: normal;
  }
  .contact-list {
    position: absolute;
    left: 198px; top: 168px;
    list-style: none;
    color: var(--text-grey);
    font-size: 12.5px;
    line-height: 16px;
  }
  .contact-list li { display: flex; align-items: center; gap: 8px; white-space: nowrap; }
  .contact-icon { width: 9px; height: 9px; flex: none; fill: var(--brand-red); }
</style>
</head>
<body>
  <section class="card card-front" aria-label="Business card front">
    <div class="wordmark"><span class="wordmark-mark"></span>Heron Haulage</div>
    <p class="holder-name">Marcus Whitfield</p>
    <address class="address">4117 W. Larkin Ave.<br>Pharr, TX 78590</address>
    <ul class="contact-list">
      <li>
        <svg class="contact-icon" viewBox="0 0 10 10" aria-hidden="true"><path d="M2.5 0h5a1 1 0 0 1 1 1v8a1 1 0 0 1-1 1h-5a1 1 0 0 1-1-1V1a1 1 0 0 1 1-1zm.5 1.5v6h4v-6z"/></svg>
        (956)238-7160
      </li>
      <li>
        <svg class="contact-icon" viewBox="0 0 10 10" aria-hidden="true"><path d="M2 .5l1.8 2-1 1.2c.6 1.3 1.5 2.2 2.8 2.8l1.2-1 2 1.8-1 1.9C4.5 9 1 5.5.3 1.5z"/></svg>
        1-855-317-6094
      </li>
      <li>
        <svg class="contact-icon" viewBox="0 0 10 10" aria-hidden="true"><path d="M0 2h10v6H0zm1 .8v.4l4 2.6 4-2.6v-.4z"/></svg>
        marcuswhitfield@heronhaulage.example
      </li>
      <li>
        <svg class="contact-icon" viewBox="0 0 10 10" aria-hidden="true"><circle cx="5" cy="5" r="5"/><path d="M0 5h10M5 0c-2 2.7-2 7.3 0 10M5 0c2 2.7 2 7.3 0 10" stroke="#fff" stroke-width=".8" fill="none"/></svg>
        www.heronhaulage.example
      </li>
    </ul>
  </section>

  <section class="card card-back" aria-label="Business card back">
    <div class="wordmark"><span class="wordmark-mark"></span>Heron Haulage</div>
  </section>
</body>
</html>
```